4 Poster Designs required for Nail Salon

We require 4 poster designs that will be displayed inside a shopping centre. Each design should contain our logo and the words "Located next to Tallmart" (or similar). Design 1 (MOTHERS DAY) should contain the words "Mothers Day Special" and "$10 gift voucher when you spend over $50". Design 2 (CHRISTMAS) should contain the words "Christmas in July" and "Purchase a set of nails and get a $10 gift voucher". Design 3 (ALL YEAR) should contain the words "New Deluxe Spa Pedicure Service" and the words "Try our new Deluxe Spa Pedicure and get a free nail buff, shape and polish for your fingernails". Design 4 (ALL YEAR 2)should contain high quality nail salon image(s) and the words "Now Open". We like designs that support our image of high quality/fun/clean and safe.
Updates
I will close this early. In 24 hours.
Target Market(s)
Rich mums
Industry/Entity Type
Shopping
Look and feel
Each slider illustrates characteristics of the customer's brand and the style your logo design should communicate.

```html
<!DOCTYPE html>
<html lang="en">
<head>
<meta charset="utf-8">
<title>Mothers Day Special Poster – Glossa Nail Salon</title>
<link rel="stylesheet" href="https://fonts.googleapis.com/css2?family=Great+Vibes&family=Roboto:wght@300;400;700&display=swap">
<style>
  :root {
    --backdrop: #ececec;
    --paper: #ffffff;
    --script-pink: #d976ad;
    --ink: #2f2f2f;
    --brand-pink-dark: #d94f9d;
    --brand-pink-light: #ec8cc0;
    --photo-skin: #f1d2c4;
    --photo-petal: #e8a3c4;
  }
  * { margin: 0; padding: 0; box-sizing: border-box; }
  html, body {
    width: 1200px;
    height: 1148px;
    overflow: hidden;
    background: var(--backdrop);
  }
  .poster {
    position: absolute;
    left: 240px;
    top: 54px;
    width: 720px;
    height: 1040px;
    background: var(--paper);
    font-family: "Roboto", Arial, sans-serif;
    color: var(--ink);
    overflow: hidden;
  }
  .hero-photo {
    position: absolute;
    left: 73px;
    top: 0;
    width: 647px;
    height: 453px;
    background:
      radial-gradient(ellipse 30% 40% at 85% 30%, var(--photo-petal) 0%, rgba(232,163,196,0) 100%),
      radial-gradient(ellipse 55% 60% at 38% 40%, var(--photo-skin) 0%, rgba(241,210,196,0) 100%),
      var(--paper);
  }
  .headline {
    position: absolute;
    font-family: "Great Vibes", cursive;
    color: var(--script-pink);
    font-weight: 400;
    line-height: 1;
    transform: rotate(-8deg);
    transform-origin: left bottom;
  }
  .headline--first { left: 160px; top: 420px; font-size: 104px; }
  .headline--second { left: 390px; top: 500px; font-size: 104px; }
  .offer {
    position: absolute;
    left: 353px;
    top: 640px;
    line-height: 1.05;
    font-size: 29px;
  }
  .offer strong { font-weight: 700; display: block; }
  .offer span { font-weight: 400; display: block; }
  .brand-block {
    position: absolute;
    left: 357px;
    top: 747px;
    width: 363px;
    height: 210px;
    background: linear-gradient(90deg, var(--brand-pink-dark), var(--brand-pink-light));
    color: #ffffff;
    font-weight: 300;
  }
  .brand-name {
    position: absolute;
    left: 60px;
    top: 62px;
    font-size: 56px;
    letter-spacing: 4px;
  }
  .brand-tag {
    position: absolute;
    right: 24px;
    top: 132px;
    font-size: 16px;
    letter-spacing: 1px;
  }
  .location {
    position: absolute;
    left: 357px;
    top: 968px;
    width: 363px;
    text-align: center;
    font-size: 14px;
    letter-spacing: 3px;
    font-weight: 400;
  }
  .location b { font-weight: 700; }
</style>
</head>
<body>
  <main class="poster">
    <div class="hero-photo" role="img" aria-label="Photo of manicured hands with French tip nails resting on a white towel beside pink orchid flowers"></div>

    <h1>
      <span class="headline headline--first">Mothers Day</span>
      <span class="headline headline--second">Special</span>
    </h1>

    <p class="offer">
      <strong>$10 GIFT VOUCHER</strong>
      <span>when you</span>
      <strong>SPEND OVER $50"</strong>
    </p>

    <div class="brand-block">
      <span class="brand-name">Glossa</span>
      <span class="brand-tag">Nail Salon</span>
    </div>

    <p class="location">LOCATED NEXT TO <b>TALLMART</b></p>
  </main>
</body>
</html>
```